indépendant en tant que Massothérapeute et Préparateur Mental, j'ai besoin de ...

Massothérapeute et préparateur mental indépendant, je recherche une carte de visite sobre et dynamique, sans images liées au massage ou à la préparation mentale mais intégrant mon logo. Les couleurs que j'aime bien sont : Blanc, gris, anthracite, noir et jaune

Contact Information for Business Card

carte de préférence Horizontale
neutre qui puisse toucher le deux domaines Massothérapie et préparation mentale

Requirements
Must have
• mon projet doit intégrer au recto:
LOGO
Loïc Bardèze
078 513 26 48
info@loicbardeze.ch
et éventuellement www.loicbardeze.ch

et au verso les deux adresses:

Chemin des Ormilles 7B
1400 Yverdon-les-Bains

Route de la Gravière 9
1700 Fribourg

Should not have
• mon projet ne doit pas contenir d'image en liens avec le massage ni la préparation mentale.

```html
<!DOCTYPE html>
<html lang="fr">
<head>
<meta charset="utf-8">
<title>Loïc Bardèze – Cartes de visite</title>
<link rel="stylesheet" href="https://fonts.googleapis.com/css2?family=Arimo:wght@400;700&display=swap">
<style>
  :root {
    --backdrop: #c8c8c8;
    --anthracite: #242424;
    --paper: #ffffff;
    --ink: #1f1d1e;
    --light: #f2f2f2;
    --accent: #f2c500;
    --muted: #6d6d6d;
  }
  * { margin: 0; padding: 0; box-sizing: border-box; }
  html, body { width: 1200px; height: 900px; overflow: hidden; }
  body {
    background: var(--backdrop);
    font-family: "Arimo", Arial, sans-serif;
    position: relative;
  }
  .card {
    position: absolute;
    left: 290px;
    width: 620px;
    height: 354px;
    border-radius: 30px;
    box-shadow: 0 6px 18px rgba(0,0,0,0.22);
  }
  .card--back { top: 80px; background: var(--anthracite); color: var(--light); }
  .card--front { top: 466px; background: var(--paper); color: var(--ink); }

  .brand { position: absolute; display: flex; align-items: center; gap: 16px; }
  .brand__dot { width: 22px; height: 22px; border-radius: 50%; background: currentColor; flex: none; }
  .brand__name { font-weight: 700; font-size: 34px; letter-spacing: 0.5px; line-height: 1; }
  .brand__role {
    margin-top: 7px; font-size: 11.5px; font-variant: small-caps;
    letter-spacing: 1.3px; text-transform: lowercase;
  }
  .card--back .brand { left: 118px; top: 92px; }
  .card--front .brand { left: 62px; top: 70px; }

  .addresses {
    position: absolute; left: 0; right: 0; top: 212px;
    text-align: center; font-size: 19px; line-height: 1.6;
  }

  .contact { position: absolute; left: 62px; bottom: 48px; list-style: none; }
  .contact__item { display: flex; align-items: center; gap: 12px; font-size: 19px; line-height: 1.55; }
  .contact__icon { width: 18px; height: 18px; flex: none; }
</style>
</head>
<body>

<section class="card card--back" aria-label="Verso">
  <div class="brand">
    <span class="brand__dot"></span>
    <div>
      <div class="brand__name">Loïc Bardèze</div>
      <div class="brand__role">Massothérapeute / Préparateur Mental</div>
    </div>
  </div>
  <div class="addresses">
    <p>Chemin des Ormilles 7B, 1400 Yverdon-les-Bains</p>
    <p>Route de la Gravière 9, 1700 Freiburg</p>
  </div>
</section>

<section class="card card--front" aria-label="Recto">
  <div class="brand">
    <span class="brand__dot"></span>
    <div>
      <div class="brand__name">Loïc Bardèze</div>
      <div class="brand__role">Massothérapeute / Préparateur Mental</div>
    </div>
  </div>
  <ul class="contact">
    <li class="contact__item">
      <svg class="contact__icon" viewBox="0 0 24 24" aria-hidden="true">
        <path fill="var(--accent)" d="M6.6 10.8a15.1 15.1 0 0 0 6.6 6.6l2.2-2.2a1 1 0 0 1 1-.25 11.4 11.4 0 0 0 3.6.57 1 1 0 0 1 1 1V20a1 1 0 0 1-1 1A17 17 0 0 1 3 4a1 1 0 0 1 1-1h3.5a1 1 0 0 1 1 1c0 1.25.2 2.45.57 3.57a1 1 0 0 1-.25 1z"/>
      </svg>
      078 513 26 48
    </li>
    <li class="contact__item">
      <svg class="contact__icon" viewBox="0 0 24 24" aria-hidden="true">
        <rect x="2" y="5" width="20" height="14" rx="1.5" fill="var(--accent)"/>
        <path d="M3 6.5l9 6.5 9-6.5" fill="none" stroke="var(--paper)" stroke-width="1.6"/>
      </svg>
      info@loicbardeze.ch
    </li>
    <li class="contact__item">
      <svg class="contact__icon" viewBox="0 0 24 24" aria-hidden="true">
        <circle cx="12" cy="12" r="10" fill="var(--accent)"/>
        <g fill="none" stroke="var(--paper)" stroke-width="1.3">
          <ellipse cx="12" cy="12" rx="4.5" ry="10"/>
          <path d="M2 12h20M4 7h16M4 17h16M12 2v20"/>
        </g>
      </svg>
      www.loicbardeze.ch
    </li>
  </ul>
</section>

</body>
</html>
```